Veltrane Group Business Card Design

The CEO is looking for a new trendy look for his business card.
You can stay with current branding or come up with something new/creative. It can be 3D, including Medical Office buildings. You can use our logo in a variety of colors. Please include name, title, company name, company website, email address, cell number

Target Market(s)

Real Estate Development and Construction

Industry/Entity Type

Health care real estate

Contact Information for Business Card

Rohesh Kamdar, CEO M-604.781.2249 E-roheshkamdar@veltrane.com Address:4180 Lindqvist Ave, Tampa, FL 33482 www.veltrane.com

Font styles to use
Other font styles liked:
• Be creative

Requirements
Must have
• Creative, trendy look
Nice to have
• Please go to our website to get a feel- www. veltrane.com
Should not have
• small fonts

```html
<!DOCTYPE html>
<html lang="en">
<head>
<meta charset="utf-8">
<title>Veltrane Group – Business Card</title>
<link rel="stylesheet" href="https://fonts.googleapis.com/css2?family=Arimo:wght@400;700&display=swap">
<style>
  :root {
    --backdrop: #3e3e3e;
    --brand-red: #b01f29;
    --card-white: #ffffff;
    --ink-white: #ffffff;
    --shadow: rgba(0, 0, 0, 0.35);
  }
  * { box-sizing: border-box; margin: 0; padding: 0; }
  html, body {
    width: 1200px;
    height: 803px;
    overflow: hidden;
    background: var(--backdrop);
    font-family: "Arimo", Arial, sans-serif;
  }
  .stage {
    position: relative;
    width: 1200px;
    height: 803px;
  }
  .card {
    position: absolute;
    top: 258px;
    width: 500px;
    height: 286px;
    border-radius: 20px;
    box-shadow: 0 14px 30px var(--shadow);
    overflow: hidden;
  }
  .card--front {
    left: 70px;
    background: var(--brand-red);
    color: var(--ink-white);
  }
  .card--back {
    left: 630px;
    background: var(--card-white);
    display: flex;
    align-items: center;
    justify-content: center;
  }
  .brand-name {
    font-weight: 700;
    letter-spacing: -0.5px;
    line-height: 1;
  }
  .card--front .brand-name {
    position: absolute;
    left: 34px;
    top: 38px;
    font-size: 40px;
    color: var(--ink-white);
  }
  .card--back .brand-name {
    font-size: 50px;
    color: var(--brand-red);
  }
  .person {
    position: absolute;
    left: 34px;
    top: 104px;
  }
  .person__name {
    font-weight: 700;
    font-size: 21px;
    letter-spacing: 0.3px;
  }
  .person__title {
    font-size: 13px;
    margin-top: 3px;
  }
  .address {
    position: absolute;
    left: 34px;
    top: 160px;
    font-size: 13px;
    line-height: 1.35;
    font-style: normal;
  }
  .contact-list {
    position: absolute;
    left: 34px;
    top: 203px;
    list-style: none;
    font-size: 13px;
    line-height: 1.45;
  }
  .contact-list li {
    display: flex;
    align-items: center;
    gap: 7px;
  }
  .contact-list svg {
    width: 11px;
    height: 11px;
    flex: none;
    fill: var(--ink-white);
  }
</style>
</head>
<body>
<main class="stage">
  <section class="card card--front" aria-label="Card front">
    <p class="brand-name">Veltrane Group</p>
    <div class="person">
      <p class="person__name">Rohesh Kamdar</p>
      <p class="person__title">CEO</p>
    </div>
    <address class="address">4180 Lindqvist Ave, Tampa<br>FL 33482</address>
    <ul class="contact-list">
      <li>
        <svg viewBox="0 0 12 12" aria-hidden="true"><path d="M2.2 0.8 L4.2 0.5 L5 3.2 L3.7 4.2 C4.4 5.8 6.1 7.6 7.8 8.3 L8.8 7 L11.5 7.8 L11.2 9.8 C10.9 11 9.6 11.6 8.4 11.2 C4.8 10 2 7.2 0.8 3.6 C0.4 2.4 1 1.1 2.2 0.8 Z"/></svg>
        <span>604.781.2249</span>
      </li>
      <li>
        <svg viewBox="0 0 12 12" aria-hidden="true"><path d="M0.5 2.5 H11.5 V9.5 H0.5 Z M1.2 3 L6 6.6 L10.8 3 Z" fill-rule="evenodd"/></svg>
        <span>roheshkamdar@veltrane.com</span>
      </li>
      <li>
        <svg viewBox="0 0 12 12" aria-hidden="true"><path d="M6 0.5 A5.5 5.5 0 1 1 5.99 0.5 Z M6 1.7 A4.3 4.3 0 1 0 6.01 1.7 Z M5.3 2 H6.7 V10 H5.3 Z M2 5.3 H10 V6.7 H2 Z" fill-rule="evenodd"/></svg>
        <span>www.veltrane.com</span>
      </li>
    </ul>
  </section>

  <section class="card card--back" aria-label="Card back">
    <p class="brand-name">Veltrane Group</p>
  </section>
</main>
</body>
</html>
```